English and Spanish Language School Needs a Business Card

Need a business card design a startup company called Maribel Language School. The company will offer English and Spanish conversational level courses designed to make the learner feel comfortable with grammar and vocabulary. We would like to see a logo with some colour that should communicate learning, growth.

Target Market(s)

Consumers and businesses

Industry/Entity Type

Education

Contact Information for Business Card

TBD

Font styles to use
Serif

Requirements
Must have
• Include the following
• Logo
• Name
• Title
• Cellphone Number
• Office Phone number
• Email address
• Office Address

```html
<!DOCTYPE html>
<html lang="en">
<head>
<meta charset="utf-8">
<title>Maribel Language School – Business Card</title>
<link href="https://fonts.googleapis.com/css2?family=Open+Sans:wght@400;600;700&display=swap" rel="stylesheet">
<style>
  :root {
    --backdrop: #ece7df;
    --card-black: #0d0d0e;
    --card-black-soft: #1a1a1c;
    --brand-red: #d02127;
    --brand-red-deep: #b81c22;
    --brand-teal: #0aa3b2;
    --text-white: #f4f4f4;
    --card-shadow: rgba(0,0,0,0.28);
  }
  * { margin: 0; padding: 0; box-sizing: border-box; }
  html, body { width: 1200px; height: 900px; overflow: hidden; }
  body {
    background: var(--backdrop);
    font-family: "Open Sans", Arial, sans-serif;
    position: relative;
  }
  .card {
    position: absolute;
    width: 600px;
    height: 343px;
    border-radius: 4px;
    overflow: hidden;
    background: radial-gradient(ellipse at 40% 35%, var(--card-black-soft), var(--card-black) 75%);
    box-shadow: 0 14px 30px var(--card-shadow);
  }
  .card--front { left: 90px; top: 110px; }
  .card--back { left: 510px; top: 440px; }

  .wordmark {
    font-weight: 700;
    color: var(--brand-red);
    letter-spacing: -0.5px;
    white-space: nowrap;
    display: flex;
    align-items: center;
    gap: 10px;
  }
  .wordmark__dot {
    width: 14px; height: 14px;
    border-radius: 50%;
    background: var(--brand-teal);
    flex: none;
  }
  .card--front .wordmark {
    position: absolute;
    left: 0; right: 0; top: 148px;
    justify-content: center;
    font-size: 34px;
  }
  .card--back .wordmark {
    position: absolute;
    right: 26px; top: 52px;
    font-size: 19px;
  }
  .card--back .wordmark__dot { width: 10px; height: 10px; }

  .contact-block {
    position: absolute;
    left: 34px; top: 30px;
    color: var(--text-white);
  }
  .person-name { color: var(--brand-red); font-weight: 600; font-size: 17px; line-height: 1.2; }
  .person-title { font-size: 14px; margin-top: 2px; }
  .contact-list { list-style: none; margin-top: 30px; }
  .contact-list li {
    display: flex; align-items: center; gap: 10px;
    font-size: 14.5px; line-height: 22px;
  }
  .contact-list svg { width: 11px; height: 11px; flex: none; fill: var(--brand-red); }
  .postal-address { font-style: normal; font-size: 15px; line-height: 22px; margin-top: 28px; }

  .accent-band {
    position: absolute;
    left: 0; right: 0; bottom: 0;
    height: 96px;
    background: linear-gradient(180deg, var(--brand-red), var(--brand-red-deep));
  }
</style>
</head>
<body>

  <section class="card card--front" aria-label="Business card front">
    <div class="wordmark"><span class="wordmark__dot"></span>Maribel Language School</div>
  </section>

  <section class="card card--back" aria-label="Business card back">
    <div class="accent-band" role="img" aria-label="Decorative red and teal wave band"></div>

    <div class="wordmark"><span class="wordmark__dot"></span>Maribel Language School</div>

    <div class="contact-block">
      <p class="person-name">Daniel Harwick</p>
      <p class="person-title">Managing Director</p>
      <ul class="contact-list">
        <li><svg viewBox="0 0 12 12"><path d="M1,4 C1,2 3,1 6,1 C9,1 11,2 11,4 L9,5 L8,3.5 C7,3 5,3 4,3.5 L3,5 Z M3,6 L9,6 L10,11 L2,11 Z"/></svg>(055) 214 378 906</li>
        <li><svg viewBox="0 0 12 12"><path d="M3,0 H9 V12 H3 Z M4,1.5 V9 H8 V1.5 Z"/></svg>(055)907321564</li>
        <li><svg viewBox="0 0 12 12"><path d="M0,2 H12 V10 H0 Z M1,3 L6,7 L11,3 Z"/></svg>hello@maribelschool.com</li>
      </ul>
      <address class="postal-address">48, Linden Row Westbrook,<br>Spain, 20417</address>
    </div>
  </section>

</body>
</html>
```